first fantastic look and impression

We are looking for a concept for letterhead, business card, emailfooter and template for invoices or offers for our company in the consultation business.
The dancer is a symbol who we are: it looks simple, but there is a lot of hard work and many years of training in this movement. The look is also what we want: elegant, modern, strong, with a touch of extravaganza
Target Market(s)
Hotelbusiness , Consulting
Font styles to use
Sans Serif
Other font styles liked:
- please give us a option we are open
Requirements
Must have
- We are not typical consultants but sparring partners and coaches for the hotel and that should also be expressed in the design. Maybe there is an icon that supports the whole thing. We are more modern and bolder than our industry colleagues.
we are modern, fresh, agile, fast
Nice to have
- a icon

```html
<!DOCTYPE html>
<html lang="de">
<head>
<meta charset="utf-8">
<title>Brandner + Partner – Visitenkarten</title>
<link rel="stylesheet" href="https://fonts.googleapis.com/css2?family=Roboto:wght@400;700&display=swap">
<style>
  :root {
    --backdrop: #d2d7d9;
    --paper: #f4f3ef;
    --ink: #141414;
    --night: #0e0e0f;
    --silver: #e9e9e9;
    --gilt: #a8883f;
    --muted: #3a3a3a;
  }
  * { box-sizing: border-box; margin: 0; padding: 0; }
  html, body {
    width: 686px; height: 1200px; overflow: hidden;
    background: var(--backdrop);
    font-family: "Roboto", Arial, sans-serif;
    color: var(--ink);
  }
  .sheet {
    width: 686px; height: 1200px;
    display: flex; flex-direction: column;
    justify-content: space-around; align-items: center;
    padding: 60px 0;
  }
  .card-set {
    display: flex; gap: 26px;
  }
  .card {
    width: 310px; height: 200px;
    position: relative;
    border-bottom: 3px solid var(--gilt);
  }
  .card--front { background: var(--paper); }
  .card--back {
    background: var(--night);
    display: flex; align-items: center; justify-content: center;
  }
  .wordmark {
    font-family: "Roboto", Arial, sans-serif;
    font-weight: 400;
    letter-spacing: 0.04em;
  }
  .card--front .wordmark {
    position: absolute; left: 24px; top: 26px;
    font-size: 17px; color: var(--ink);
  }
  .card--back .wordmark {
    font-size: 27px; color: var(--silver);
  }
  .contact {
    position: absolute; left: 150px; bottom: 24px;
  }
  .contact__name {
    font-weight: 700; font-size: 10.5px;
    letter-spacing: 0.02em; text-transform: uppercase;
  }
  .contact__rule {
    width: 12px; height: 1.5px; background: var(--ink);
    margin: 9px 0 8px;
  }
  .contact__list { list-style: none; }
  .contact__item {
    display: flex; align-items: center; gap: 5px;
    font-size: 8.5px; line-height: 12.5px; color: var(--muted);
  }
  .contact__icon { width: 9px; height: 9px; flex: none; }
</style>
</head>
<body>
<main class="sheet">

  <section class="card-set">
    <article class="card card--front">
      <span class="wordmark">Brandner + Partner</span>
      <div class="contact">
        <p class="contact__name">Lena Brandner</p>
        <div class="contact__rule"></div>
        <ul class="contact__list">
          <li class="contact__item"><svg class="contact__icon" viewBox="0 0 10 10"><circle cx="5" cy="5" r="5" fill="#141414"/><path d="M5 2.2a1.8 1.8 0 0 1 1.8 1.8C6.8 5.4 5 7.8 5 7.8S3.2 5.4 3.2 4A1.8 1.8 0 0 1 5 2.2z" fill="#fff"/></svg>6830 Rankweil / Lindenweg 12</li>
          <li class="contact__item"><svg class="contact__icon" viewBox="0 0 10 10"><circle cx="5" cy="5" r="5" fill="#141414"/><rect x="3.3" y="2.2" width="3.4" height="5.6" rx="0.6" fill="#fff"/></svg>+43 660 4817230</li>
          <li class="contact__item"><svg class="contact__icon" viewBox="0 0 10 10"><circle cx="5" cy="5" r="5" fill="#141414"/><path d="M3 2.5l1.2 1.2-.6.8a4 4 0 0 0 1.9 1.9l.8-.6L7.5 7l-.8.8C5 7.8 2.2 5 2.2 3.3z" fill="#fff"/></svg>+43 660 5129384</li>
          <li class="contact__item"><svg class="contact__icon" viewBox="0 0 10 10"><circle cx="5" cy="5" r="5" fill="#141414"/><rect x="2.4" y="3.2" width="5.2" height="3.6" fill="none" stroke="#fff" stroke-width="0.8"/><path d="M2.4 3.2L5 5.2l2.6-2" fill="none" stroke="#fff" stroke-width="0.8"/></svg>lb@brandnerpartner.example</li>
          <li class="contact__item"><svg class="contact__icon" viewBox="0 0 10 10"><circle cx="5" cy="5" r="5" fill="#141414"/><circle cx="5" cy="5" r="2.6" fill="none" stroke="#fff" stroke-width="0.7"/><path d="M2.4 5h5.2M5 2.4v5.2" stroke="#fff" stroke-width="0.6"/></svg>brandnerpartner.example</li>
        </ul>
      </div>
    </article>
    <article class="card card--back">
      <span class="wordmark">Brandner + Partner</span>
    </article>
  </section>

  <section class="card-set">
    <article class="card card--front">
      <span class="wordmark">Brandner + Partner</span>
      <div class="contact">
        <p class="contact__name">Jonas Brandner</p>
        <div class="contact__rule"></div>
        <ul class="contact__list">
          <li class="contact__item"><svg class="contact__icon" viewBox="0 0 10 10"><circle cx="5" cy="5" r="5" fill="#141414"/><path d="M5 2.2a1.8 1.8 0 0 1 1.8 1.8C6.8 5.4 5 7.8 5 7.8S3.2 5.4 3.2 4A1.8 1.8 0 0 1 5 2.2z" fill="#fff"/></svg>6830 Rankweil / Lindenweg 12</li>
          <li class="contact__item"><svg class="contact__icon" viewBox="0 0 10 10"><circle cx="5" cy="5" r="5" fill="#141414"/><rect x="3.3" y="2.2" width="3.4" height="5.6" rx="0.6" fill="#fff"/></svg>+43 660 5129384</li>
          <li class="contact__item"><svg class="contact__icon" viewBox="0 0 10 10"><circle cx="5" cy="5" r="5" fill="#141414"/><path d="M3 2.5l1.2 1.2-.6.8a4 4 0 0 0 1.9 1.9l.8-.6L7.5 7l-.8.8C5 7.8 2.2 5 2.2 3.3z" fill="#fff"/></svg>+43 660 5129384</li>
          <li class="contact__item"><svg class="contact__icon" viewBox="0 0 10 10"><circle cx="5" cy="5" r="5" fill="#141414"/><rect x="2.4" y="3.2" width="5.2" height="3.6" fill="none" stroke="#fff" stroke-width="0.8"/><path d="M2.4 3.2L5 5.2l2.6-2" fill="none" stroke="#fff" stroke-width="0.8"/></svg>jb@brandnerpartner.example</li>
          <li class="contact__item"><svg class="contact__icon" viewBox="0 0 10 10"><circle cx="5" cy="5" r="5" fill="#141414"/><circle cx="5" cy="5" r="2.6" fill="none" stroke="#fff" stroke-width="0.7"/><path d="M2.4 5h5.2M5 2.4v5.2" stroke="#fff" stroke-width="0.6"/></svg>brandnerpartner.example</li>
        </ul>
      </div>
    </article>
    <article class="card card--back">
      <span class="wordmark">Brandner + Partner</span>
    </article>
  </section>

</main>
</body>
</html>
```